Cloud-based vaccination website

Basic website design for cloud-based medical company

Coding

Coded - Design and coding required

Number of Pages Required

1 page

Colors
3277b5

```html
<!DOCTYPE html>
<html lang="en">
<head>
<meta charset="utf-8">
<title>NIMBOVA – Modern Digital Software Solutions</title>
<link href="https://fonts.googleapis.com/css2?family=Montserrat:wght@400;500;600;700&family=Roboto:wght@400;500&display=swap" rel="stylesheet">
<style>
:root{
  --navy:#0f1f5a;
  --navy-deep:#0b1a5c;
  --cyan:#1ba3d6;
  --cyan-bright:#22c4f0;
  --brand:#3277b5;
  --text:#555b66;
  --white:#ffffff;
  --line:#d9edf3;
}
*{margin:0;padding:0;box-sizing:border-box}
html,body{width:1200px;height:3525px;overflow:hidden}
body{position:relative;background:var(--white);font-family:'Roboto',Arial,sans-serif;color:var(--text)}
.abs{position:absolute}
.head{font-family:'Montserrat',Arial,sans-serif;color:var(--navy);font-weight:600}
.accent{color:var(--cyan)}
.btn{position:absolute;display:flex;align-items:center;justify-content:center;border-radius:30px;background:var(--cyan);color:var(--white);font-family:'Montserrat',Arial,sans-serif;font-weight:500;text-transform:uppercase}

/* header */
.site-header{position:absolute;left:0;top:0;width:1200px;height:131px;background:var(--white);z-index:3}
.brand{position:absolute;left:112px;top:44px;display:flex;align-items:center;gap:10px;font-family:'Montserrat',Arial,sans-serif;font-weight:700;font-size:34px;color:var(--navy)}
.brand-dot{width:22px;height:22px;border-radius:50%;background:var(--cyan)}
.nav{position:absolute;top:60px;font-family:'Montserrat',Arial,sans-serif;font-size:14px;font-weight:500;color:var(--navy)}
.nav.active{color:var(--cyan)}

/* hero */
.hero-art{position:absolute;left:0;top:131px}
.hero-title{position:absolute;left:678px;top:212px;font-family:'Montserrat',Arial,sans-serif;font-weight:500;font-size:74px;color:var(--white);letter-spacing:1px}
.hero-sub{position:absolute;left:680px;top:302px;font-family:'Montserrat',Arial,sans-serif;font-weight:500;font-size:21px;color:var(--white)}

/* section titles */
.section-title{position:absolute;left:0;width:1200px;text-align:center;font-size:38px}
.rule{position:absolute;height:3px;background:var(--cyan)}

/* services */
.card{position:absolute;top:1015px;width:308px;height:374px;border:1px solid var(--line);background:var(--white);box-shadow:0 6px 18px rgba(27,163,214,.12);text-align:center}
.card svg{position:absolute;left:99px;top:30px}
.card h3{position:absolute;top:165px;width:100%;font-size:21px}
.card p{position:absolute;top:202px;left:20px;width:266px;font-size:14px;line-height:26px}
.card .btn{left:85px;top:299px;width:137px;height:46px;font-size:15px}

/* welcome */
.welcome-title{position:absolute;left:112px;top:1513px;font-size:35px}
.welcome-copy{position:absolute;left:112px;top:1591px;width:443px;font-size:14px;line-height:25.8px;text-align:justify}
.welcome-art{position:absolute;left:575px;top:1477px;width:625px;height:493px;background:radial-gradient(ellipse at 60% 45%,#c9d4f7 0%,#e8ecfb 45%,#ffffff 75%)}

/* vaccination */
.vax-band{position:absolute;left:0;top:1970px;width:1200px;height:524px;background:linear-gradient(100deg,#1fd3f3 0%,#18b6e6 45%,#139fd8 100%)}
.vax-title{position:absolute;left:702px;top:2098px;font-family:'Montserrat',Arial,sans-serif;font-weight:500;font-size:34px;color:var(--white)}
.vax-copy{position:absolute;left:702px;top:2160px;width:430px;font-size:13.6px;line-height:27.5px;color:var(--white)}

/* blog */
.post-img{position:absolute;top:2642px;width:313px;height:232px}
.post-date{position:absolute;top:2892px;font-family:'Montserrat',Arial,sans-serif;font-weight:500;font-size:20px;color:var(--cyan)}
.post-title{position:absolute;top:2932px;font-family:'Montserrat',Arial,sans-serif;font-weight:500;font-size:18px;color:var(--navy)}
.post-copy{position:absolute;top:2966px;width:313px;font-size:14px;line-height:26px}

/* footer */
.site-footer{position:absolute;left:0;top:3101px;width:1200px;height:424px;background:var(--navy-deep);color:var(--white)}
.foot-brand{position:absolute;left:140px;top:3270px;display:flex;align-items:center;gap:14px;font-family:'Montserrat',Arial,sans-serif;font-weight:700;font-size:62px;color:var(--white)}
.foot-brand .brand-dot{width:34px;height:34px}
.foot-title{position:absolute;font-family:'Montserrat',Arial,sans-serif;font-weight:500;font-size:22px;color:var(--white)}
.foot-text{position:absolute;font-size:15px;line-height:23px;color:var(--white);letter-spacing:.5px}
.foot-icon{position:absolute}
.email-field{position:absolute;left:762px;top:3287px;width:326px;height:41px;background:var(--white);border-radius:2px;padding-left:18px;display:flex;align-items:center;font-size:15px;color:#666}
.copyright{position:absolute;left:0;top:3474px;width:1200px;text-align:center;font-size:15px;color:var(--white)}
</style>
</head>
<body>

<header class="site-header">
  <div class="brand"><span class="brand-dot"></span>NIMBOVA</div>
  <span class="nav active" style="left:578px">HOME</span>
  <span class="nav" style="left:669px">ABOUT US</span>
  <span class="nav" style="left:789px">SERVICES</span>
  <span class="nav" style="left:907px">NEWS</span>
  <span class="nav" style="left:999px">CONTACT US</span>
</header>

<svg class="hero-art" width="1200" height="724" viewBox="0 0 1200 724" role="img" aria-label="Illustration of a glowing cloud server linked to a world map on a deep blue background">
  <defs>
    <linearGradient id="heroFill" x1="0" y1="0" x2="1" y2="1">
      <stop offset="0" stop-color="#0a1f86"/>
      <stop offset="0.45" stop-color="#0c2fb8"/>
      <stop offset="1" stop-color="#081a78"/>
    </linearGradient>
    <radialGradient id="heroGlow" cx="0.3" cy="0.35" r="0.4">
      <stop offset="0" stop-color="#2a7cf0" stop-opacity=".7"/>
      <stop offset="1" stop-color="#2a7cf0" stop-opacity="0"/>
    </radialGradient>
  </defs>
  <path d="M0,0 H1200 V283 C950,400 700,540 470,640 C300,712 150,730 0,650 Z" fill="url(#heroFill)"/>
  <path d="M0,0 H1200 V283 C950,400 700,540 470,640 C300,712 150,730 0,650 Z" fill="url(#heroGlow)"/>
  <path d="M0,650 C150,730 300,712 470,640 C700,540 950,400 1200,283" fill="none" stroke="#1fa6e0" stroke-width="8"/>
</svg>
<div class="hero-title">NIMBOVA</div>
<div class="hero-sub">MODERN DIGITAL SOFTWARE SOLUTIONS</div>
<div class="btn" style="left:680px;top:356px;width:176px;height:56px;font-size:17px">Read More</div>

<h2 class="section-title head" style="top:905px">OUR <span class="accent">SERVICES</span></h2>
<div class="rule" style="left:582px;top:962px;width:37px"></div>

<div class="card" style="left:112px">
  <svg width="110" height="100" viewBox="0 0 110 100" fill="none" stroke="#1d3a7a" stroke-width="3">
    <rect x="5" y="5" width="32" height="24" fill="#cfe6f8"/><rect x="73" y="5" width="32" height="24" fill="#cfe6f8"/>
    <rect x="5" y="64" width="32" height="24" fill="#cfe6f8"/><rect x="73" y="64" width="32" height="24" fill="#cfe6f8"/>
    <path d="M37 17 H73 M37 76 H73 M21 29 V44 M89 29 V44 M21 64 V56 M89 64 V56"/>
    <path d="M40 58 a9 9 0 0 1 5 -16 a12 12 0 0 1 22 3 a7 7 0 0 1 2 13 Z" fill="#8fc6f0"/>
  </svg>
  <h3 class="head">SERVICES 01</h3>
  <p>Sed ut perspiciatis unde omnis iste nat us error sit voluptatem accusantium laudantium totam aperia</p>
  <div class="btn">Read More</div>
</div>
<div class="card" style="left:446px">
  <svg width="110" height="100" viewBox="0 0 110 100" fill="none" stroke="#1d3a7a" stroke-width="3">
    <rect x="18" y="3" width="74" height="26" fill="#a9d4f5"/><rect x="18" y="33" width="74" height="26" fill="#a9d4f5"/><rect x="18" y="63" width="74" height="26" fill="#a9d4f5"/>
    <circle cx="78" cy="16" r="5"/><circle cx="78" cy="46" r="5"/><circle cx="78" cy="76" r="5"/>
    <path d="M28 12 h6 M28 20 h6 M40 12 h6 M40 20 h6 M28 42 h6 M28 50 h6 M40 42 h6 M40 50 h6 M28 72 h6 M28 80 h6 M40 72 h6 M40 80 h6 M55 89 V97 M18 97 H92"/>
  </svg>
  <h3 class="head">SERVICES 02</h3>
  <p>Sed ut perspiciatis unde omnis iste nat us error sit voluptatem accusantium laudantium totam aperia</p>
  <div class="btn">Read More</div>
</div>
<div class="card" style="left:780px">
  <svg width="130" height="100" viewBox="0 0 130 100" fill="none" stroke="#1d3a7a" stroke-width="3" style="left:88px">
    <circle cx="45" cy="45" r="40"/><ellipse cx="45" cy="45" rx="18" ry="40"/>
    <path d="M5 45 H85 M12 25 H78 M12 65 H78 M45 5 V85"/>
    <path d="M58 88 a13 13 0 0 1 6 -25 a18 18 0 0 1 33 5 a11 11 0 0 1 3 20 Z" fill="#8fc6f0"/>
  </svg>
  <h3 class="head">SERVICES 03</h3>
  <p>Sed ut perspiciatis unde omnis iste nat us error sit voluptatem accusantium laudantium totam aperia</p>
  <div class="btn">Read More</div>
</div>

<h2 class="welcome-title head">WELCOME TO <span class="accent">NIMBOVA</span></h2>
<div class="rule" style="left:112px;top:1568px;width:59px;background:var(--navy)"></div>
<p class="welcome-copy">Sed ut perspiciatis unde omnis iste natus error sit voluptatem accus antium doloremque laudantium, totam rem aperiam, eaque ipsa quae ab illo inventore veritatis et quasi architecto beatae vitae dicta sunt explicabo. Nemo enim ipsam voluptatem quia voluptas sit aspernatur aut odit aut fugit, sed quia consequuntur magni dolores eos qui ratione voluptatem sequi nesciunt. Neque porro quisquam est, qui dolorem ipsum audantium, totam remquia dolor sit amet, sed ut perspiciatis unde omnis iste natus error sit voluptatem accus antium doloremque laudantium, totam rem quasi architecto beatae vitae dicta sunt explicabo</p>
<div class="btn" style="left:111px;top:1854px;width:156px;height:52px;font-size:16px">Read More</div>
<div class="welcome-art" role="img" aria-label="Isometric illustration of a cloud data centre connected to desktop computers"></div>

<div class="vax-band" role="img" aria-label="Photo of a patient receiving a vaccine injection in the upper arm, tinted cyan"></div>
<div class="vax-title">VACCINATION SERVICES</div>
<p class="vax-copy">Sed ut perspiciatis unde omnis iste natus error sit voluptatem accusa ntium doloremque laudantium, totam rem aperiam, eaque ipsa quae architecto beatae vitae dicta sunt explicabo.</p>
<div class="btn" style="left:702px;top:2268px;width:161px;height:54px;font-size:16px;background:var(--navy)">Read More</div>

<h2 class="section-title head" style="top:2550px">LATEST <span class="accent">BLOG</span></h2>
<div class="rule" style="left:582px;top:2604px;width:37px"></div>

<div class="post-img" style="left:111px;background:linear-gradient(135deg,#6b6a5a,#d8d2b8 60%,#f3efe0)" role="img" aria-label="Photo of hands sketching a network diagram beside a laptop"></div>
<div class="post-img" style="left:443px;background:linear-gradient(135deg,#3a4048,#8e949c 55%,#2a2e34)" role="img" aria-label="Photo of two colleagues with a laptop in a server room"></div>
<div class="post-img" style="left:776px;background:linear-gradient(135deg,#2a4a8a,#6a7fb8 50%,#1a2f66)" role="img" aria-label="Photo of hands typing on a laptop with blue binary code overlay"></div>

<div class="post-date" style="left:111px">24 MAR 2021</div>
<div class="post-date" style="left:443px">24 MAR 2021</div>
<div class="post-date" style="left:776px">24 MAR 2021</div>
<div class="post-title" style="left:111px">Nemo enim ipsam voluptatem</div>
<div class="post-title" style="left:443px">Nemo enim ipsam voluptatem</div>
<div class="post-title" style="left:776px">Nemo enim ipsam voluptatem</div>
<p class="post-copy" style="left:111px">Sed ut perspiciatis unde omnis iste natus error sit voluptatem accusantium doloremque lauda ntium, totam rem aperiam</p>
<p class="post-copy" style="left:443px">Sed ut perspiciatis unde omnis iste natus error sit voluptatem accusantium doloremque lauda ntium, totam rem aperiam</p>
<p class="post-copy" style="left:776px">Sed ut perspiciatis unde omnis iste natus error sit voluptatem accusantium doloremque lauda ntium, totam rem aperiam</p>

<footer class="site-footer"></footer>
<div class="foot-brand"><span class="brand-dot"></span>NIMBOVA</div>

<div class="foot-title" style="left:484px;top:3166px">CONTACT US</div>
<svg class="foot-icon" style="left:487px;top:3232px" width="18" height="24" viewBox="0 0 18 24" fill="none" stroke="#fff" stroke-width="1.6"><path d="M9 23 C4 16 1.5 12 1.5 8.5 a7.5 7.5 0 0 1 15 0 C16.5 12 14 16 9 23Z"/><circle cx="9" cy="8.5" r="2.8"/></svg>
<div class="foot-text" style="left:525px;top:3218px">Address<br>#215 Lorem Ipsum<br>Dummy Text Lorem</div>
<svg class="foot-icon" style="left:486px;top:3306px" width="20" height="20" viewBox="0 0 20 20" fill="none" stroke="#fff" stroke-width="1.6"><path d="M4 1.5 l3 4 -2 2.5 c1.5 3 4 5.5 7 7 l2.5 -2 4 3 -2 3 C8 18 2 12 1 4 Z"/></svg>
<div class="foot-text" style="left:525px;top:3308px">Phone :<br>000-121-1231</div>
<svg class="foot-icon" style="left:486px;top:3398px" width="22" height="16" viewBox="0 0 22 16" fill="none" stroke="#fff" stroke-width="1.6"><rect x="1" y="1" width="20" height="14"/><path d="M1 1 L11 9 L21 1"/></svg>
<div class="foot-text" style="left:525px;top:3397px">Email :<br>info@company.com</div>

<div class="foot-title" style="left:762px;top:3162px">NEWSLETTER</div>
<div class="foot-text" style="left:762px;top:3214px;width:340px;font-size:14px;line-height:26px;letter-spacing:0">Sed ut perspiciatis unde omnis iste natus error sit voluptatem accusantium doloremque</div>
<div class="email-field">Enter Email</div>
<div class="btn" style="left:761px;top:3346px;width:143px;height:45px;font-size:15px">Subscribe</div>

<div class="copyright">© Copyright 2021.All Rights Reserved</div>

</body>
</html>
```